Tusk Hollow Lodge website (design only)

Tusk Hollow Lodge (http://www.tuskhollowlodge-mw.example) is a private Safari lodge located in Malawi.
We would like a modern, professional website designed that does not subscribe to the cliched view of a Safari in Africa, but still maintain a wildlife/safari atmosphere.

The aim of our website is to entice people & drive them to the booking form.

Here are some examples of websites that we like. Although we would like our site to be a bit more in line with modern web design trends.

http://www.marulaplains.example/
http://www.kovunde.example/
http://www.tembalorecamp.example/

Requirements
Must have
• Here is a list of the pages required. Most of them will follow a standard content layout. I.e. heading, body and images.

If you take a look at the website, you will get an idea of hoe many page types there are +- 5

http://www.tuskhollowlodge-mw.example/index.htm

About Tusk Hollow
Lirundu Country Club
Rooms
Conferences
Cuisine
Facilities
Your Safari
Activities
Rates & Special Offers
Booking form
Latest Developments
How To Get There
Gallery
Contact Us
Blog / Newsfeed

```html
<!DOCTYPE html>
<html lang="en">
<head>
<meta charset="utf-8">
<title>Tusk Hollow Lodge</title>
<link rel="stylesheet" href="https://fonts.googleapis.com/css2?family=Great+Vibes&family=Cinzel:wght@600&family=Arimo:wght@400&display=swap">
<style>
:root{
  --bg:#2f2a25;
  --panel:#877a57;
  --nav-ink:#2a251f;
  --cream:#d9cfb8;
  --tagline:#a4977a;
  --heading:#c8b88c;
  --body:#a8a095;
  --link:#cdbb8a;
  --rule:#6e6452;
}
*{box-sizing:border-box;margin:0;padding:0}
html,body{width:1200px;height:899px;overflow:hidden;background:var(--bg)}
body{position:relative;font-family:"Arimo",Arial,sans-serif}
.brand{position:absolute;left:52px;top:30px;color:var(--cream)}
.brand-name{font-family:"Arimo",Arial,sans-serif;font-weight:400;font-size:40px;line-height:46px;letter-spacing:1px;color:var(--cream)}
.brand-place{font-size:11.5px;letter-spacing:1px;margin:6px 0 0 66px;color:var(--cream)}
.tagline{position:absolute;right:52px;top:42px;font-family:"Great Vibes",cursive;font-size:33px;color:var(--tagline)}
.stage{position:absolute;left:55px;top:127px;width:1094px;height:505px;background:var(--panel)}
.nav{display:flex;height:33px;align-items:center;background:linear-gradient(#978a64,#7f7352);padding-left:6px}
.nav a{font-size:13.5px;color:var(--nav-ink);text-decoration:none;padding:0 15px;height:33px;line-height:33px;position:relative}
.nav a+a::before{content:"";position:absolute;left:0;top:11px;height:12px;width:1px;background:#5c523b}
.nav a.active{background:#a69870}
.hero{position:absolute;left:7px;top:35px;width:1078px;height:364px;
  background:linear-gradient(180deg,#4a4233 0%,#6d7a86 35%,#7f97ab 55%,#c8a867 80%,#b08a45 100%)}
.thumbs{position:absolute;left:0;top:411px;width:100%;height:82px}
.thumb{position:absolute;top:0;width:140px;height:81px;border:2px solid #e8e0cc}
.arrow{position:absolute;top:34px;color:#e8e0cc;font-size:13px}
.col{position:absolute;top:647px}
.col h2{font-family:"Cinzel",serif;font-weight:600;font-size:13.5px;color:var(--heading);text-align:center;white-space:nowrap;
  border-top:1px solid var(--rule);border-bottom:1px solid var(--rule);height:46px;line-height:44px;letter-spacing:.3px}
.col p{font-size:12.4px;line-height:16.2px;color:var(--body);margin-top:12px}
.col .links{font-size:12.4px;line-height:16.2px;color:var(--link)}
.col .links span{color:var(--body);padding:0 8px}
.divider{position:absolute;top:650px;width:1px;height:168px;background:#3f3931}
.footer{position:absolute;left:0;top:868px;width:1200px;height:31px;background:var(--panel);
  font-size:12.5px;color:var(--nav-ink);line-height:31px}
.footer-text{position:absolute;left:323px;top:0;white-space:nowrap}
.social{position:absolute;left:50px;top:0;height:31px;display:flex;align-items:center}
.social .ico{width:46px;display:flex;justify-content:center;border-right:1px solid #6f6446}
</style>
</head>
<body>
<header class="brand">
  <div class="brand-name">Tusk Hollow Lodge</div>
  <div class="brand-place">NKHALANGO ESTATE &nbsp;|&nbsp; MZENGA</div>
</header>
<div class="tagline">Experience the endless beauty of Nature</div>

<section class="stage">
  <nav class="nav">
    <a class="active">Home</a><a>About</a><a>Gallery</a><a>Safari</a><a>Lodge</a><a>Activities</a><a>Rates &amp; Specials</a><a>Bookings</a><a>Developments</a><a>Directions</a><a>Blog</a><a>Contact</a>
  </nav>
  <div class="hero" role="img" aria-label="Giraffe walking through golden grassland under a dramatic cloudy sky"></div>
  <div class="thumbs">
    <span class="arrow" style="left:11px">&#8249;</span>
    <div class="thumb" role="img" aria-label="Zebras close up" style="left:31px;background:linear-gradient(135deg,#ddd,#555)"></div>
    <div class="thumb" role="img" aria-label="Waterbuck among trees" style="left:181px;background:linear-gradient(#8a9a5a,#6b7a3a)"></div>
    <div class="thumb" role="img" aria-label="Antelope herd on open plains" style="left:331px;background:linear-gradient(#a8b8c8,#7a8a4a)"></div>
    <div class="thumb" role="img" aria-label="River winding through wetland" style="left:481px;background:linear-gradient(#b9c6c8,#5a8ab0 55%,#7a8a4a)"></div>
    <div class="thumb" role="img" aria-label="Impala portrait" style="left:631px;background:linear-gradient(#e9e9e6,#a6784a)"></div>
    <div class="thumb" role="img" aria-label="Elephants crossing water" style="left:781px;background:linear-gradient(#9ab2c8,#6a7a6a)"></div>
    <div class="thumb" role="img" aria-label="Antelope grazing near trees" style="left:931px;background:linear-gradient(#9ab0c0,#6a8a3a)"></div>
    <span class="arrow" style="left:1076px">&#8250;</span>
  </div>
</section>

<article class="col" style="left:58px;width:230px">
  <h2>TUSK HOLLOW LODGE</h2>
  <p>Warmest welcome to the unique Malawi experience: lodge complex, game park, the 18 hole Lirundu golf club &amp; Chisoni dam. Tusk Hollow Lodge provides all the holiday and business prerequisites in a beautiful, relaxing environment.</p>
  <div class="links">Read more...</div>
</article>
<div class="divider" style="left:318px"></div>
<article class="col" style="left:350px;width:216px">
  <h2>GAME &amp; WILD BIRDS</h2>
  <p>Lorem ipsum dolor sit amet, consect etuer adipiscing elit, sed diam nonum my nibh euismod tincidunt ut laoreet dolore magna aliquam erat volutpat. Ut wisi enim ad minim veniam quis no strud exerci tatin ullamcorper suscipit</p>
  <div class="links">Read more<span>|</span>Booking Enquiry</div>
</article>
<div class="divider" style="left:598px"></div>
<article class="col" style="left:631px;width:220px">
  <h2>THE LODGE &amp; ROOMS</h2>
  <p style="width:216px">Lorem ipsum dolor sit amet, consect etuer adipiscing elit, sed diam nonum my nibh euismod tincidunt ut laoreet dolore magna aliquam erat volutpat. Ut wisi enim ad minim veniam quis no strud exerci tatin ullamcorper suscipit</p>
  <div class="links">Read more<span>|</span>Booking Enquiry</div>
</article>
<div class="divider" style="left:884px"></div>
<article class="col" style="left:920px;width:223px">
  <h2>CONFERENCE &amp; RESTURANT</h2>
  <p style="width:216px">Lorem ipsum dolor sit amet, consect etuer adipiscing elit, sed diam nonum my nibh euismod tincidunt ut laoreet dolore magna aliquam erat volutpat. Ut wisi enim ad minim veniam quis no strud exerci tatin ullamcorper suscipit</p>
  <div class="links">Read more<span>|</span>Booking Enquiry</div>
</article>

<footer class="footer">
  <div class="social">
    <span class="ico"><svg width="12" height="12"><circle cx="6" cy="6" r="5" fill="#3e372c"/></svg></span>
    <span class="ico"><svg width="12" height="12"><circle cx="6" cy="6" r="5" fill="#3e372c"/></svg></span>
    <span class="ico"><svg width="12" height="12"><circle cx="6" cy="6" r="5" fill="#3e372c"/></svg></span>
    <span class="ico" style="border-right:0"><svg width="16" height="12" viewBox="0 0 16 12"><rect x="1" y="1" width="14" height="10" fill="none" stroke="#3e372c" stroke-width="1.5"/><path d="M1 1l7 6 7-6" fill="none" stroke="#3e372c" stroke-width="1.5"/></svg></span>
  </div>
  <div class="footer-text">Tusk Hollow Lodge copyright © 2012 &nbsp;|&nbsp; Privacy Policy &nbsp;|&nbsp; Blog &nbsp;|&nbsp; Contact &nbsp;|&nbsp; Booking Enquiries</div>
</footer>
</body>
</html>
```